Velvet Lantern rebranding my business with a new business card

I have my new logo and now I need a refresher on my business cards. I really want something fun and fresh. I like black background or anything to make the color pop.
Logo
Name: Velvet Lantern
Contact Info as stated below:
Mira Pellow
555-013-4762
Logo
Name: Velvet Lantern
Mira Pellow
555-013-4762
fb.me/VelvetLanternbyMira
Instagram: @VelvetLanternbyMira

Industry/Entity Type

Business

Contact Information for Business Card

double-sided. Logo on one side. Contact info on the other.

Requirements
Must have
• Logo
• Name: Velvet Lantern
• Contact Info as stated below:
• Mira Pellow
• 555-013-4762
• fb.me/VelvetLanternbyMira
• fb.me/VelvetLanternbyMira

```html
<!DOCTYPE html>
<html lang="en">
<head>
<meta charset="utf-8">
<title>Velvet Lantern – Business Card</title>
<link href="https://fonts.googleapis.com/css2?family=Open+Sans:wght@400;600&display=swap" rel="stylesheet">
<style>
  :root{
    --backdrop:#2b2b2b;
    --teal:#3bbfa8;
    --teal-deep:#2fae98;
    --red:#b5202c;
    --blush:#f2b8c6;
    --ink:#3a3a3a;
    --paper:#ffffff;
  }
  *{margin:0;padding:0;box-sizing:border-box}
  html,body{width:1200px;height:930px;overflow:hidden;background:var(--backdrop);font-family:"Open Sans",sans-serif}
  .stage{position:relative;width:1200px;height:930px}
  .card{position:absolute;width:580px;height:332px;border-radius:18px;overflow:hidden;box-shadow:0 14px 30px rgba(0,0,0,.45)}
  .card-front{left:90px;top:100px;background:linear-gradient(160deg,#4cc9b3,var(--teal-deep));display:flex;align-items:center;justify-content:center}
  .brand-mark{font-size:34px;font-weight:600;color:var(--paper);letter-spacing:1px}
  .card-back{left:530px;top:500px;background:var(--paper)}
  .logo-badge{position:absolute;left:60px;top:70px;width:150px;height:150px;border-radius:50%;border:3px solid var(--blush);display:flex;align-items:center;justify-content:center;text-align:center}
  .logo-badge span{font-size:20px;font-weight:600;color:var(--ink);line-height:1.2}
  .divider{position:absolute;left:250px;top:60px;width:1.5px;height:150px;background:var(--red)}
  .contact{position:absolute;left:280px;top:60px}
  .person-name{font-size:25px;font-weight:400;color:var(--teal);letter-spacing:1px;text-transform:uppercase;line-height:1}
  .person-role{font-size:15px;color:var(--ink);margin-top:4px}
  .contact-list{list-style:none;margin-top:10px}
  .contact-list li{display:flex;align-items:center;gap:10px;font-size:16px;color:var(--ink);line-height:26px}
  .contact-list svg{width:13px;height:13px;flex:none}
  .wave{position:absolute;left:0;bottom:0;width:580px;height:332px}
</style>
</head>
<body>
<main class="stage">
  <section class="card card-front" aria-label="Card front">
    <div class="brand-mark">Velvet Lantern</div>
  </section>

  <section class="card card-back" aria-label="Card back">
    <div class="logo-badge"><span>Velvet<br>Lantern</span></div>
    <div class="divider"></div>
    <div class="contact">
      <p class="person-name">Mira Pellow</p>
      <p class="person-role">Owner</p>
      <ul class="contact-list">
        <li><svg viewBox="0 0 12 12"><rect x="3" y="0.5" width="6" height="11" rx="1.2" fill="none" stroke="#3bbfa8" stroke-width="1.2"/></svg>555-013-4762</li>
        <li><svg viewBox="0 0 12 12"><rect x="0.5" y="2" width="11" height="8" fill="#3bbfa8"/><path d="M0.5 2 L6 7 L11.5 2" fill="none" stroke="#fff" stroke-width="1"/></svg>info@mirapellow.com</li>
        <li><svg viewBox="0 0 12 12"><rect x="0" y="0" width="12" height="12" rx="2" fill="#3bbfa8"/></svg>fb.me/VelvetLanternbyMira</li>
      </ul>
    </div>
    <svg class="wave" viewBox="0 0 580 332" preserveAspectRatio="none" aria-hidden="true">
      <path d="M120 332 C200 220 330 300 430 250 C500 215 550 185 580 150 L580 332 Z" fill="#3bbfa8"/>
      <path d="M110 332 C190 212 325 285 425 236 C495 200 545 170 580 132 L580 142 C548 178 500 208 430 244 C330 294 198 216 116 332 Z" fill="#b5202c"/>
    </svg>
  </section>
</main>
</body>
</html>
```